Brightfen Business Card Redesign & Logo Update

We need to update our business cards to something more modern and fresh. Brightfen can provide the current color schemes and old design examples, but welcome creativity in helping us with this redesign. PLEASE NOTE that we no longer utilize the "tree" and/or "leaf" imagery in our branding. If able would apprecaite an update on the quality of our "words only" logo in Ai. / PNG formats too.

Target Market(s)

Investors, landowners, corporate partners, contractors

Industry/Entity Type

Environmental Restoration & Conservation

Contact Information for Business Card

Logo, persons name, title, mailing address, phone and email, website url

Font styles to use
Other font styles liked:
• Merriweather

Requirements
Nice to have
• Logo, persons name, title, mailing address, phone and email, website url, but open to ideams
Should not have
• No all back backgrounds

```html
<!DOCTYPE html>
<html lang="en">
<head>
<meta charset="utf-8">
<title>Brightfen Business Card</title>
<link rel="stylesheet" href="https://fonts.googleapis.com/css2?family=Merriweather:wght@400;700;900&display=swap">
<style>
  :root {
    --backdrop: #d2d3d5;
    --card: #ffffff;
    --green: #1b8640;
    --orange: #f08a24;
    --ink: #231f20;
  }
  * { box-sizing: border-box; margin: 0; padding: 0; }
  html, body { width: 900px; height: 1200px; overflow: hidden; }
  body {
    background: var(--backdrop);
    font-family: "Merriweather", Georgia, serif;
    color: var(--ink);
    position: relative;
  }
  .card {
    position: absolute;
    left: 120px;
    width: 660px;
    height: 380px;
    background: var(--card);
  }
  .card--front { top: 202px; }
  .card--back { top: 619px; }

  .wordmark {
    font-weight: 900;
    color: var(--green);
    letter-spacing: 2px;
    line-height: 1;
  }
  .tagline {
    font-weight: 700;
    font-size: 13px;
    letter-spacing: 1.6px;
    color: var(--ink);
    text-transform: uppercase;
  }

  .front-brand {
    position: absolute;
    top: 132px;
    left: 0;
    width: 100%;
    text-align: center;
  }
  .front-brand .wordmark { font-size: 62px; }
  .front-brand .tagline { margin-top: 14px; font-size: 15px; }

  .social {
    position: absolute;
    top: 317px;
    left: 0;
    width: 100%;
    display: flex;
    justify-content: center;
    gap: 13px;
  }
  .social__dot {
    width: 32px; height: 32px; border-radius: 50%;
    background: var(--green);
  }
  .social__dot--accent { background: var(--orange); }

  .back-brand {
    position: absolute;
    top: 40px;
    left: 41px;
  }
  .back-brand .wordmark { font-size: 46px; }
  .back-brand .tagline { margin-top: 10px; font-size: 11.5px; letter-spacing: 1.2px; }

  .person {
    position: absolute;
    top: 38px;
    right: 42px;
    text-align: right;
  }
  .person__name { font-weight: 700; font-size: 27px; line-height: 1.2; }
  .person__title { font-size: 16px; color: var(--green); margin-top: 2px; }

  .contact {
    position: absolute;
    left: 40px;
    top: 270px;
    list-style: none;
    font-size: 16.5px;
    line-height: 24px;
    letter-spacing: 0.3px;
  }
  .contact li { display: flex; align-items: center; gap: 6px; }
  .contact svg { width: 14px; height: 14px; flex: none; fill: var(--green); }

  .address {
    position: absolute;
    right: 40px;
    top: 294px;
    text-align: right;
    font-size: 16.5px;
    line-height: 24px;
    font-style: normal;
    letter-spacing: 0.3px;
  }
</style>
</head>
<body>
  <section class="card card--front" aria-label="Card front">
    <div class="front-brand">
      <div class="wordmark">BRIGHTFEN</div>
      <div class="tagline">Environmental Credit Company</div>
    </div>
    <div class="social" aria-label="Social media links">
      <span class="social__dot"></span>
      <span class="social__dot social__dot--accent"></span>
      <span class="social__dot"></span>
    </div>
  </section>

  <section class="card card--back" aria-label="Card back">
    <div class="back-brand">
      <div class="wordmark">BRIGHTFEN</div>
      <div class="tagline">Environmental Credit Company</div>
    </div>
    <div class="person">
      <div class="person__name">Dana Holloway</div>
      <div class="person__title">Director</div>
    </div>
    <ul class="contact">
      <li>
        <svg viewBox="0 0 16 16" aria-hidden="true"><path d="M3.6 1.2l2.2 2.9-1.3 1.6c.9 2 2.3 3.4 4.2 4.3l1.6-1.3 2.9 2.2-1.1 2.6C7 13.2 2.8 9 2.3 2.3z"/></svg>
        (555) 014-2287
      </li>
      <li>
        <svg viewBox="0 0 16 16" aria-hidden="true"><path d="M1 3h14v1.4L8 9 1 4.4z"/><path d="M1 6.2l7 4.5 7-4.5V13H1z"/></svg>
        info@brightfencredits.com
      </li>
      <li>
        <svg viewBox="0 0 16 16" aria-hidden="true"><path d="M8 1a7 7 0 100 14A7 7 0 008 1zm0 1.5c.8 0 1.8 1.6 2.1 4H5.9C6.2 4.1 7.2 2.5 8 2.5zM2.6 7.5h1.9c0 .8.1 1.5.2 2.2H3.1a5.5 5.5 0 01-.5-2.2zm2.9 0h5c0 .8-.1 1.5-.2 2.2H5.7a11 11 0 01-.2-2.2zm6 0h1.9c0 .8-.2 1.5-.5 2.2h-1.6c.1-.7.2-1.4.2-2.2zM8 13.5c-.8 0-1.6-1.1-2-2.8h4c-.4 1.7-1.2 2.8-2 2.8z"/></svg>
        www.brightfencredits.com
      </li>
    </ul>
    <address class="address">
      4870 County Road 318<br>
      Marlow, TX 75990
    </address>
  </section>
</body>
</html>
```